Classy, Elegant, Simple Business Card Design

Looking to have a classy, simple, and elegant design. Want a top notch designed business card. I really like the look of the new torvane credit card. I also like the design I attached. I am trying to reach 21-29 year old females for booking us for there wedding or event. We offer Disc Jockey Service, Photo Booth Rentals, and Uplighting .

Target Market(s)

21-28 year old females

Contact Information for Business Card

Has to have logo, website, email, and phone number

Font styles to use
Other font styles liked:
• open to font choice, modern, clean
Designer to choose
33a6d7
0791cd
0555a3
ffffff

Requirements
Must have
• Has to have logo, website, email, and phone number
Nice to have
• I really like the design of the new torvane credit card. I also included my logo and some designs I like
Should not have
• clutter or too much info

```html
<!DOCTYPE html>
<html lang="en">
<head>
<meta charset="utf-8">
<title>Brightnote Event Group – Business Card</title>
<link rel="stylesheet" href="https://fonts.googleapis.com/css2?family=Poppins:wght@300;400;500&display=swap">
<style>
  :root {
    --page-bg: #e9e6e2;
    --card-top: #f4f4f5;
    --card-bottom: #e4e6ea;
    --brand-blue: #0555a3;
    --name-blue: #0a3f78;
    --ink-grey: #5a5a5e;
    --text-dark: #1f2a3a;
    --navy-deep: #0b1a38;
    --navy-mid: #123a6e;
    --wave-silver: #c9ccd2;
    --wave-blue: #1d5ea8;
    --service-silver: #b9bcc4;
  }
  * { margin: 0; padding: 0; box-sizing: border-box; }
  html, body {
    width: 1200px;
    height: 969px;
    overflow: hidden;
    background: var(--page-bg);
    font-family: "Poppins", sans-serif;
  }
  .card {
    position: absolute;
    left: 100px;
    top: 199px;
    width: 1000px;
    height: 571px;
    background: linear-gradient(180deg, var(--card-top), var(--card-bottom));
    box-shadow: 0 10px 30px rgba(0, 0, 0, 0.18);
    overflow: hidden;
  }
  .card__wave {
    position: absolute;
    inset: 0;
    width: 1000px;
    height: 571px;
  }
  .brand {
    position: absolute;
    left: 120px;
    top: 205px;
    width: 340px;
    text-align: center;
    color: var(--brand-blue);
    font-weight: 500;
    font-size: 40px;
    line-height: 1.15;
    letter-spacing: 1px;
  }
  .brand__line { display: block; }
  .brand__line--small { font-size: 40px; }
  .divider {
    position: absolute;
    left: 479px;
    top: 150px;
    width: 2px;
    height: 180px;
    background: var(--text-dark);
  }
  .contact {
    position: absolute;
    left: 527px;
    top: 148px;
  }
  .contact__name {
    color: var(--name-blue);
    font-weight: 500;
    font-size: 32px;
    line-height: 42px;
    margin-left: 1px;
  }
  .contact__title {
    color: var(--ink-grey);
    font-weight: 400;
    font-size: 21px;
    line-height: 28px;
    margin-left: 1px;
  }
  .contact__list {
    list-style: none;
    margin-top: 24px;
  }
  .contact__item {
    display: flex;
    align-items: center;
    height: 29px;
    color: var(--text-dark);
    font-size: 22px;
    font-weight: 400;
  }
  .contact__icon {
    width: 22px;
    height: 22px;
    margin-right: 12px;
    flex: none;
  }
  .services {
    position: absolute;
    right: 110px;
    top: 478px;
    text-align: right;
    color: var(--service-silver);
    font-size: 21px;
    font-weight: 400;
    line-height: 28px;
  }
</style>
</head>
<body>
  <div class="card">
    <svg class="card__wave" viewBox="0 0 1000 571" aria-hidden="true">
      <defs>
        <linearGradient id="bandFill" x1="0" y1="0" x2="1" y2="0">
          <stop offset="0" stop-color="#1a3f75"/>
          <stop offset="0.5" stop-color="#0d1f42"/>
          <stop offset="1" stop-color="#0b1a38"/>
        </linearGradient>
      </defs>
      <path d="M0 470 C120 500 200 520 300 512 C460 500 620 430 780 432 C880 434 950 470 1000 490 L1000 571 L0 571 Z" fill="url(#bandFill)"/>
      <path d="M0 462 C120 492 200 512 300 504 C460 492 620 422 780 424 C880 426 950 462 1000 482" fill="none" stroke="var(--wave-blue)" stroke-width="6"/>
      <path d="M0 452 C110 485 210 500 320 490 C480 476 630 415 790 418 C890 420 955 452 1000 470" fill="none" stroke="var(--wave-silver)" stroke-width="2"/>
      <path d="M0 478 C130 505 210 524 310 518 C470 508 630 440 785 440 C880 442 950 476 1000 496" fill="none" stroke="var(--wave-silver)" stroke-width="1.5" opacity="0.8"/>
    </svg>

    <div class="brand">
      <span class="brand__line">BRIGHTNOTE</span>
      <span class="brand__line brand__line--small">EVENT GROUP</span>
    </div>

    <div class="divider"></div>

    <div class="contact">
      <p class="contact__name">Daniel Reyes</p>
      <p class="contact__title">President</p>
      <ul class="contact__list">
        <li class="contact__item">
          <svg class="contact__icon" viewBox="0 0 24 24" aria-hidden="true"><path fill="var(--name-blue)" d="M6.6 10.8a15 15 0 0 0 6.6 6.6l2.2-2.2a1 1 0 0 1 1-.25 11.4 11.4 0 0 0 3.6.57 1 1 0 0 1 1 1V20a1 1 0 0 1-1 1A17 17 0 0 1 3 4a1 1 0 0 1 1-1h3.5a1 1 0 0 1 1 1c0 1.25.2 2.45.57 3.6a1 1 0 0 1-.25 1z"/></svg>
          555-014-2287
        </li>
        <li class="contact__item">
          <svg class="contact__icon" viewBox="0 0 24 24" aria-hidden="true"><rect x="2" y="5" width="20" height="14" rx="1.5" fill="var(--name-blue)"/><path d="M3 6.5l9 6.5 9-6.5" fill="none" stroke="#f0f0f2" stroke-width="1.6"/></svg>
          hello@brightnoteevents.com
        </li>
        <li class="contact__item">
          <svg class="contact__icon" viewBox="0 0 24 24" aria-hidden="true"><circle cx="12" cy="12" r="10" fill="var(--name-blue)"/><path d="M7 8c2 0 3 1 3 3s-2 2-2 4M14 5c-1 2 1 3 3 3M15 14c1 1 2 2 1 4" fill="none" stroke="#f0f0f2" stroke-width="1.6" stroke-linecap="round"/></svg>
          www.brightnoteevents.com
        </li>
      </ul>
    </div>

    <div class="services">
      <p>Disc Jockey Service</p>
      <p>Photo Booth Rentals • Uplighting</p>
    </div>
  </div>
</body>
</html>
```